Harborline Lending and Capital. We provide MOSTLY residential home mortgages in Florida AND commercial loans for investment properties throughout the United states.
I would love to emulate so of the lender sites that are available on the internet but I would like to have the site as popular as possible for SEO purposes. Clients can already click the link to take them to the mortgage application where they can complete that and upload documents. If you could polish that up for me that would be great. I can also provide you with great detail on loan programs that are currently being offered. WE OFFER ALL MORTGAGE LENDING PRODUCTS. I would also like to add something in reference to the rate but I don't think it's legal to actually state or promise a rate for mortgage since they vary based on loan type, client and other criteria...

On the Harborline real estate site I would like to add a link or some way for clients to be able to put in credit card information to render services ...

Please let me know what you need from me

Thank you !!

Current link to site to improve and code

https://harborlinelendingandcapital.example/

Industry/Entity Type

Residential and commmercial lending

Coding

Coded - Design and coding required

Number of Pages Required

2 page

Requirements
Must have
• Love to integrate Mortgage interest rates even if general
Nice to have
• Link to fill out mortgage application via Quorvel LPX software

```html
<!DOCTYPE html>
<html lang="en">
<head>
<meta charset="utf-8">
<title>Harborline Lending and Capital</title>
<link href="https://fonts.googleapis.com/css2?family=Montserrat:wght@500;600;700;800&family=Lato:wght@400;700&display=swap" rel="stylesheet">
<style>
:root{
  --green-deep:#173d24;
  --green:#1f4d2c;
  --green-mid:#2e6b3c;
  --lime:#9cc43e;
  --lime-soft:#b7e36a;
  --ink:#1b1b1b;
  --muted:#4a4a4a;
  --paper:#ffffff;
  --mist:#f1f3f1;
  --night:#121212;
}
*{margin:0;padding:0;box-sizing:border-box}
html,body{width:1200px;height:3362px;overflow:hidden;background:var(--paper)}
body{position:relative;font-family:'Lato',sans-serif;color:var(--ink)}
.abs{position:absolute}
h1,h2,h3,.mont{font-family:'Montserrat',sans-serif}

/* header */
.site-header{position:absolute;left:0;top:0;width:1200px;height:89px;background:var(--paper);border-top:4px solid var(--lime)}
.brand{position:absolute;left:111px;top:26px;display:flex;align-items:center;gap:12px}
.brand-dot{width:34px;height:34px;border-radius:50%;background:var(--green)}
.brand-name{font-family:'Montserrat',sans-serif;font-weight:700;font-size:15px;color:var(--green)}
.nav{position:absolute;left:553px;top:36px;display:flex;gap:46px;font-family:'Montserrat',sans-serif;font-weight:500;font-size:16px;color:var(--ink)}
.nav .active{color:var(--lime)}
.phone-btn{position:absolute;left:887px;top:23px;width:201px;height:46px;border-radius:23px;background:var(--green-deep);border:3px solid var(--lime);color:#fff;font-family:'Montserrat',sans-serif;font-weight:600;font-size:15px;display:flex;align-items:center;justify-content:center;gap:14px}

/* hero */
.hero{position:absolute;left:0;top:89px;width:1200px;height:600px;background:linear-gradient(100deg,#3d4a36 0%,#6a6a52 38%,#a08360 62%,#c9a98a 82%,#d9c2a8 100%)}
.hero-shade{position:absolute;inset:0;background:linear-gradient(90deg,rgba(20,25,18,.55) 0%,rgba(20,25,18,.25) 50%,rgba(0,0,0,0) 75%)}
.hero h1{position:absolute;left:111px;top:134px;width:560px;font-weight:700;font-size:45px;line-height:52px;color:#fff;text-transform:uppercase}
.hero-sub{position:absolute;left:111px;top:350px;width:420px;font-family:'Montserrat',sans-serif;font-weight:500;font-size:16px;line-height:31px;color:#fff;text-transform:uppercase}
.hero-cta{position:absolute;left:111px;top:421px;width:452px;height:47px;border-radius:24px;background:var(--green-deep);border:3px solid var(--lime);color:#fff;font-family:'Montserrat',sans-serif;font-weight:800;font-size:13.5px;display:flex;align-items:center;padding-left:24px}

/* section titles */
.sec-title{position:absolute;left:0;width:1200px;text-align:center;font-weight:800;font-size:34px;color:var(--green)}
.sec-rule{position:absolute;left:578px;width:44px;height:3px;background:var(--green)}
.sec-rule.lime{background:var(--lime);width:52px;left:574px}

/* rates */
.rates-sub{position:absolute;left:0;top:822px;width:1200px;text-align:center;font-size:16px;color:var(--ink)}
.rate{position:absolute;width:200px;text-align:center}
.bag{margin:0 auto;background:var(--green-deep);border-radius:46% 46% 14% 14% / 30% 30% 12% 12%;position:relative;display:flex;flex-direction:column;align-items:center;justify-content:flex-end;color:#fff;font-family:'Montserrat',sans-serif;font-weight:600}
.bag .pill{background:var(--lime);border-radius:8px;padding:2px 14px;margin-bottom:12px;font-size:11px}
.bag .amt{line-height:1.75}
.rate-cap{margin-top:14px;font-size:17px;line-height:27px;color:var(--ink)}

/* about */
.about{position:absolute;left:0;top:1226px;width:1200px;height:554px;background:linear-gradient(110deg,#1d4529 0%,#163a22 100%)}
.about-photo{position:absolute;left:166px;top:86px;width:370px;height:370px;border-radius:50%;border:4px solid var(--lime);background:linear-gradient(180deg,#9fc3d8 0%,#6b8a5a 45%,#8a6a4a 65%,#5f9a3c 100%)}
.about h2{position:absolute;left:631px;top:100px;font-weight:700;font-size:35px;line-height:42px;color:#fff;text-transform:uppercase}
.about-rule{position:absolute;left:631px;top:178px;width:58px;height:3px;background:var(--lime)}
.about p{position:absolute;left:632px;top:198px;width:452px;font-size:15px;line-height:27.4px;color:#fff}
.outline-btn{position:absolute;left:631px;top:405px;width:155px;height:46px;border:2px solid var(--lime);border-radius:23px;color:#fff;font-family:'Montserrat',sans-serif;font-weight:600;font-size:16px;display:flex;align-items:center;justify-content:center}

/* properties */
.prop{position:absolute;width:226px;text-align:center}
.prop-photo{width:226px;height:245px;border-radius:0 34px 0 34px}
.prop-name{margin-top:22px;font-family:'Montserrat',sans-serif;font-weight:700;font-size:17px;color:var(--ink);letter-spacing:.3px}

/* loan program */
.loan{position:absolute;left:0;top:2347px;width:1200px;height:568px;background:var(--mist)}
.loan p{position:absolute;left:111px;width:430px;font-size:15.5px;line-height:31px;color:var(--muted)}
.pie-label{font-family:'Montserrat',sans-serif;font-weight:600;font-size:13px}

/* footer */
.footer{position:absolute;left:0;top:2915px;width:1200px;height:447px;background:var(--night);color:#fff}
.footer h3{position:absolute;font-weight:600;font-size:26px;color:#fff}
.f-divider{position:absolute;top:88px;width:0;height:238px;border-left:1px dashed #777}
.links{position:absolute;left:98px;top:100px;list-style:none}
.links li{display:flex;align-items:center;gap:12px;font-size:15px;height:31px}
.contact-item{position:absolute;left:356px;width:240px;font-family:'Montserrat',sans-serif}
.contact-item .ico{position:absolute;left:0;top:6px;width:32px;height:32px;border-radius:50%;background:var(--lime);display:flex;align-items:center;justify-content:center}
.contact-item .k{margin-left:44px;font-weight:600;font-size:17px}
.contact-item .v{margin-left:44px;font-size:15px;margin-top:8px}
.contact-item.rule{border-bottom:1px dashed #888;padding-bottom:14px}
.field{position:absolute;left:715px;width:353px;height:40px;border:1px solid #bbb;border-radius:3px;color:#ddd;font-family:'Montserrat',sans-serif;font-size:14px;padding:11px 12px}
.submit{position:absolute;left:715px;top:261px;width:353px;height:38px;background:var(--lime);color:#fff;font-family:'Montserrat',sans-serif;font-weight:600;font-size:16px;display:flex;align-items:center;justify-content:center;border-radius:2px}
.f-bottom{position:absolute;left:98px;top:387px;width:1004px;height:1px;background:#888}
.copy{position:absolute;left:0;top:405px;width:1200px;text-align:center;font-family:'Montserrat',sans-serif;font-size:14px}
</style>
</head>
<body>

<header class="site-header">
  <div class="brand"><span class="brand-dot"></span><span class="brand-name">Harborline Lending and Capital</span></div>
  <nav class="nav"><span class="active">HOME</span><span>ABOUT</span><span>PROPERTIES</span></nav>
  <div class="phone-btn">
    <svg width="16" height="16" viewBox="0 0 24 24"><path fill="#fff" d="M6.6 10.8a15.1 15.1 0 0 0 6.6 6.6l2.2-2.2a1 1 0 0 1 1-.25 11.4 11.4 0 0 0 3.6.57 1 1 0 0 1 1 1V20a1 1 0 0 1-1 1A17 17 0 0 1 3 4a1 1 0 0 1 1-1h3.5a1 1 0 0 1 1 1c0 1.25.2 2.46.57 3.6a1 1 0 0 1-.25 1z"/></svg>
    +1 555 014 2290
  </div>
</header>

<section class="hero" role="img" aria-label="Stacks of coins beside a small model house on a wooden table">
  <div class="hero-shade"></div>
  <h1>Your best resource for hassle-free, low cost mortgage origination</h1>
  <div class="hero-sub">Residential home loans in Florida and commercial lending in America</div>
  <div class="hero-cta">FILL OUT MORTGAGE APPLICATION TO BEGIN LENDING PR</div>
</section>

<h2 class="sec-title" style="top:758px">MORTGAGE INTEREST RATES</h2>
<div class="sec-rule" style="top:806px"></div>
<div class="rates-sub">HARBORLINE LENDING AND CAPITAL</div>

<div class="rate" style="left:120px;top:932px">
  <div class="bag" role="img" aria-label="Money bag illustration" style="width:122px;height:155px;font-size:10px;padding-bottom:8px"><span class="pill">25%</span><span class="amt">$25.00 - $45.00<br>$25.00 - $45.00</span></div>
  <div class="rate-cap">We are strategically<br>partnered</div>
</div>
<div class="rate" style="left:370px;top:910px">
  <div class="bag" role="img" aria-label="Money bag illustration" style="width:146px;height:177px;font-size:11px;padding-bottom:10px"><span class="pill">45%</span><span class="amt">$25.00 - $45.00<br>$25.00 - $45.00</span></div>
  <div class="rate-cap">We are strategically<br>partnered</div>
</div>
<div class="rate" style="left:619px;top:873px">
  <div class="bag" role="img" aria-label="Money bag illustration" style="width:176px;height:214px;font-size:14px;padding-bottom:12px"><span class="pill">75%</span><span class="amt">$25.00 - $45.00<br>$25.00 - $45.00</span></div>
  <div class="rate-cap">We are strategically<br>partnered</div>
</div>
<div class="rate" style="left:867px;top:873px">
  <div class="bag" role="img" aria-label="Money bag illustration" style="width:176px;height:214px;font-size:14px;padding-bottom:12px"><span class="pill">85%</span><span class="amt">$25.00 - $45.00<br>$25.00 - $45.00</span></div>
  <div class="rate-cap">We are strategically<br>partnered</div>
</div>

<section class="about">
  <div class="about-photo" role="img" aria-label="Modern timber and black house with a large tree and lawn"></div>
  <h2>About Harborline<br>Lending and Capital</h2>
  <div class="about-rule"></div>
  <p>Harborline Lending Originates Residential Home loans in Florida and Commercial and business financing in all 50 States. We have over 25 years of experience in ALL types of real estate and commercial lending. We are strategically partnered to help you obtain ALL necessary components of residential and commercial lending. From the RIGHT lending partners to the best practice Insurance avenues and commercial and residential real estate partners</p>
  <div class="outline-btn">Read More</div>
</section>

<h2 class="sec-title" style="top:1860px">AVAILABLE PROPERTIES</h2>
<div class="sec-rule lime" style="top:1910px"></div>

<div class="prop" style="left:111px;top:1977px">
  <div class="prop-photo" role="img" aria-label="Modern house facade with balcony and brick wall" style="background:linear-gradient(160deg,#d8d8d4 0%,#9a9690 50%,#5a4a3c 100%)"></div>
  <div class="prop-name">12 SUNSET STREET</div>
</div>
<div class="prop" style="left:360px;top:1942px">
  <div class="prop-photo" role="img" aria-label="Dark modern house with timber entrance" style="background:linear-gradient(160deg,#2a3138 0%,#1e2428 55%,#a8743e 100%)"></div>
  <div class="prop-name">34 UNION AVENUE</div>
</div>
<div class="prop" style="left:609px;top:1977px">
  <div class="prop-photo" role="img" aria-label="Modern house with a blue swimming pool" style="background:linear-gradient(180deg,#b8cfe0 0%,#c9b596 50%,#2fb2cf 100%)"></div>
  <div class="prop-name">56 WASHINGTON</div>
</div>
<div class="prop" style="left:861px;top:1942px">
  <div class="prop-photo" role="img" aria-label="Modern facade with red timber and dark panels" style="background:linear-gradient(110deg,#8a4a36 0%,#5a5e62 55%,#7fb0de 100%)"></div>
  <div class="prop-name">78 OAK BOULEVARD</div>
</div>

<section class="loan">
  <h2 class="sec-title" style="top:68px">OUR LOAN PROGRAM</h2>
  <div class="sec-rule lime" style="top:121px"></div>
  <p style="top:176px">Harborline Lending Originates Residential Home loans in Florida and Commercial and business financing in all 50 States. We have over 25 years of experience in ALL types of real estate and commercial lending.</p>
  <p style="top:330px;width:410px">We are strategically partnered to help you obtain ALL necessary components of residential and commercial lending. From the RIGHT lending partners to the best practice Insurance avenues and commercial and residential real estate partners</p>
  <svg class="abs" style="left:560px;top:153px" width="590" height="360" viewBox="0 0 590 360" role="img" aria-label="Pie chart of living expenses, taxes, savings and debt">
    <path d="M251,169 L251,315 A146,146 0 0 1 238.3,23.6 Z" fill="#1f6a45"/>
    <path d="M254,163 L259,17 A146,146 0 0 1 373,79 Z" fill="#62b85a"/>
    <path d="M271,168 L400,99.5 A146,146 0 0 1 403.3,229.7 Z" fill="#b3f56a"/>
    <path d="M251,169 L377.4,242 A146,146 0 0 1 263.7,314.4 Z" fill="#a9aba9"/>
    <g stroke="#1f6a45" stroke-width="1.5" fill="none">
      <path d="M78,79 L100,79 L124,104"/>
      <path d="M370,52 L330,52"/>
      <path d="M400,135 L436,135"/>
    </g>
    <path d="M420,280 L398,280 L382,262" stroke="#888" stroke-width="1.5" fill="none"/>
    <circle cx="78" cy="79" r="3" fill="#1f6a45"/>
    <circle cx="370" cy="52" r="3" fill="#1f6a45"/>
    <circle cx="436" cy="135" r="3" fill="#1f6a45"/>
    <circle cx="420" cy="280" r="3" fill="#888"/>
    <text class="pie-label" x="16" y="62" fill="#1f6a45">LIVING EXPENSES</text>
    <text class="pie-label" x="386" y="56" fill="#1f6a45">TAXES</text>
    <text class="pie-label" x="423" y="119" fill="#2fa84a" font-size="18">15%</text>
    <text class="pie-label" x="481" y="140" fill="#2fa84a">SAVINGS</text>
    <text class="pie-label" x="422" y="284" fill="#777">DEBT</text>
  </svg>
</section>

<footer class="footer">
  <h3 style="left:98px;top:58px">Quick Links</h3>
  <ul class="links">
    <li><svg width="14" height="14" viewBox="0 0 14 14"><path d="M1 6h8V2l5 5-5 5V8H1z" fill="#fff"/></svg>Home</li>
    <li><svg width="14" height="14" viewBox="0 0 14 14"><path d="M1 6h8V2l5 5-5 5V8H1z" fill="#fff"/></svg>About Us</li>
    <li><svg width="14" height="14" viewBox="0 0 14 14"><path d="M1 6h8V2l5 5-5 5V8H1z" fill="#fff"/></svg>Services</li>
    <li><svg width="14" height="14" viewBox="0 0 14 14"><path d="M1 6h8V2l5 5-5 5V8H1z" fill="#fff"/></svg>Blog</li>
    <li><svg width="14" height="14" viewBox="0 0 14 14"><path d="M1 6h8V2l5 5-5 5V8H1z" fill="#fff"/></svg>Contact Us</li>
  </ul>
  <div class="f-divider" style="left:301px"></div>

  <h3 style="left:356px;top:58px">Contact Details</h3>
  <div class="contact-item rule" style="top:108px">
    <span class="ico"><svg width="14" height="14" viewBox="0 0 24 24"><path fill="#fff" d="M6.6 10.8a15.1 15.1 0 0 0 6.6 6.6l2.2-2.2a1 1 0 0 1 1-.25 11.4 11.4 0 0 0 3.6.57 1 1 0 0 1 1 1V20a1 1 0 0 1-1 1A17 17 0 0 1 3 4a1 1 0 0 1 1-1h3.5a1 1 0 0 1 1 1c0 1.25.2 2.46.57 3.6a1 1 0 0 1-.25 1z"/></svg></span>
    <div class="k">Phone:</div><div class="v">+1 555 014 2290</div>
  </div>
  <div class="contact-item rule" style="top:190px">
    <span class="ico"><svg width="14" height="12" viewBox="0 0 14 12"><rect x="0" y="1" width="14" height="10" rx="1" fill="#fff"/><path d="M0 2l7 5 7-5" stroke="#9cc43e" stroke-width="1.4" fill="none"/></svg></span>
    <div class="k">Email:</div><div class="v">hello@harborlinelending.example</div>
  </div>
  <div class="contact-item" style="top:282px">
    <span class="ico"><svg width="12" height="16" viewBox="0 0 12 16"><path d="M6 0a6 6 0 0 0-6 6c0 4.5 6 10 6 10s6-5.5 6-10a6 6 0 0 0-6-6z" fill="#fff"/><circle cx="6" cy="6" r="2.2" fill="#9cc43e"/></svg></span>
    <div class="k">Address:</div><div class="v">Harborline Lending, Tampa, Florida</div>
  </div>
  <div class="f-divider" style="left:670px"></div>

  <h3 style="left:715px;top:58px">Contact Me</h3>
  <div class="field" style="top:101px">Name:</div>
  <div class="field" style="top:155px">Email:</div>
  <div class="field" style="top:207px">Address:</div>
  <div class="submit">Submit Now</div>

  <div class="f-bottom"></div>
  <div class="copy">Copyrights@2025.Harborline Lending.All Rights Reserved</div>
</footer>

</body>
</html>
```